My name is Delia Okonkwo,I want to create a web page for my personal dog grooming business. The name on the web page can be "Delia's Dog Grooming" I am located in San Antonio Texas. The page would help grow my customer base. Before and after pictures would display the quality of work that I do. On my page I can provide information about myself, my services, and pricing.
Updates

I have updated project to guaranteed pay

Please try to incorporate a schnauzer in an icon or logo. My dog is a schnauzer. THANKS!!!!!!!!!!!!

Target Market(s)

Dog Owners

Industry/Entity Type

Business

Requirements
Must have
• -A spot for before and after pictures.
-An about me section
-A section to make an appointment
Nice to have
• My favorite Color is purple. I think different shades of purple would be nice or purple with a light green

please incorporate a schnauzer in any icon or logo. My dog is a schnauzer.

```html
<!DOCTYPE html>
<html lang="en">
<head>
<meta charset="utf-8">
<title>Delia's Dog Grooming</title>
<link rel="stylesheet" href="https://fonts.googleapis.com/css2?family=Source+Sans+3:wght@400;600;700&display=swap">
<style>
:root{
  --purple:#7b1468;
  --purple-dark:#6a0f5c;
  --purple-soft:#9a5a8e;
  --purple-text:#6b1a63;
  --lavender:#f4eff8;
  --lavender-deep:#ece1f0;
  --green-text:#4f7f1f;
  --green-dark:#3c5a17;
  --footer-top:#e6f3d8;
  --footer-bottom:#f1f8e8;
  --line:#c9c9c9;
  --ink:#222;
}
*{box-sizing:border-box;margin:0;padding:0}
html,body{width:848px;height:1200px;overflow:hidden}
body{position:relative;background:#fff;font-family:"Source Sans 3",Arial,sans-serif;color:var(--ink)}
.abs{position:absolute}

/* header */
.site-header{left:0;top:0;width:848px;height:220px;background:var(--purple);border-top:6px solid #8f3a84}
.brand{left:24px;top:30px;display:flex;align-items:center;gap:12px}
.brand-mark{width:48px;height:48px;border-radius:50%;background:#e7c9e3}
.brand-name{color:#fff;font-weight:700;font-size:20px;line-height:22px}
.main-nav{left:270px;top:73px;display:flex;gap:0}
.main-nav a{display:block;height:19px;line-height:19px;font-size:12px;color:#fff;text-decoration:none;text-align:center}
.main-nav a.active{background:#fff;color:var(--purple);border-radius:4px;width:70px}

/* hero */
.hero{left:16px;top:100px;width:814px;height:296px;background:#fff;border:3px solid var(--purple)}
.hero-panel{left:2px;top:8px;width:804px;height:276px;background:var(--lavender)}
.hero-title{left:24px;top:40px;font-size:23px;font-weight:700;color:var(--purple-text)}
.hero-punch{left:24px;top:70px;font-size:18px;font-weight:700;color:var(--purple-soft)}
.hero-copy{left:24px;top:102px;width:300px;font-size:9.6px;line-height:12.2px;color:var(--purple-text)}
.hero-copy p+p{margin-top:4px}
.btn{display:block;background:var(--purple);color:#fff;font-size:9.5px;text-align:center;border-radius:4px;text-transform:uppercase}
.hero-btn{left:24px;top:205px;width:148px;height:17px;line-height:17px}
.hero-photo{left:356px;top:18px;width:428px;height:226px;border:5px solid #fff;box-shadow:2px 4px 8px rgba(0,0,0,.3);transform:rotate(-1deg);background:linear-gradient(180deg,#6e8a4a 0%,#8a8a7a 45%,#5e8a3a 100%)}
.slider-nav{left:674px;top:256px;display:flex;align-items:center;gap:3px}
.slider-nav span{width:7px;height:7px;border-radius:50%;background:var(--purple)}
.hero-shadow{left:130px;top:400px;width:560px;height:10px;background:radial-gradient(ellipse at center,rgba(0,0,0,.18),transparent 70%)}

/* content */
.section-title{font-size:17px;color:var(--purple-text);font-weight:400}
.dotted{border-bottom:1px dotted var(--purple-soft)}
.about-title{left:24px;top:441px;width:504px;height:27px}
.about-copy{left:24px;top:478px;width:506px;font-size:9.4px;line-height:12.3px;color:var(--purple-text)}
.about-copy p+p{margin-top:4px}
.gallery-title{left:20px;top:624px;width:514px;height:26px;font-size:15px}
.gallery{left:22px;top:663px;display:grid;grid-template-columns:repeat(4,118px);grid-auto-rows:108px;column-gap:13px;row-gap:21px}
.thumb{border:2px solid #d6d6d6;background:linear-gradient(160deg,#6d6d6d,#a8a8a0 55%,#4f6b3a)}
.thumb.alt{background:linear-gradient(160deg,#b24a4a,#c9c1b2 55%,#7a6a5a)}
.view-all{left:22px;top:915px;font-size:11px;color:var(--ink)}
.divider{left:562px;top:440px;width:1px;height:460px;background:#e2e2e2}

/* sidebar */
.appointment{left:586px;top:442px;width:234px;height:156px;background:linear-gradient(90deg,var(--lavender-deep),var(--lavender));box-shadow:0 3px 5px rgba(0,0,0,.12)}
.appointment h2{position:absolute;left:15px;top:12px;width:204px;height:26px;font-size:16px;font-weight:400;color:var(--purple-text);border-bottom:1px solid #dccbe0}
.appointment p{position:absolute;left:15px;top:44px;width:208px;font-size:9.4px;line-height:12.4px;color:var(--purple-text)}
.appointment .btn{position:absolute;left:15px;top:121px;width:136px;height:16px;line-height:16px;border-radius:8px}
.rec-title{left:587px;top:634px;font-size:16px}
.rec-item{left:588px;display:flex;gap:10px}
.rec-thumb{width:68px;height:60px;border:2px solid #d6d6d6;background:linear-gradient(160deg,#5e6a7a,#9a9a98 60%,#6a7a5a)}
.rec-item h3{font-size:10px;font-weight:400;color:var(--green-dark);margin-top:1px}
.rec-item p{width:150px;font-size:9.4px;line-height:12.4px;color:var(--green-text);margin-top:4px}

/* footer */
.site-footer{left:0;top:955px;width:848px;height:245px;background:linear-gradient(180deg,var(--footer-top),var(--footer-bottom))}
.foot-head{font-size:12px;color:var(--ink);text-transform:uppercase}
.foot-links{list-style:none;width:130px}
.foot-links li{font-size:11px;color:var(--green-dark);height:21px;line-height:19px;border-bottom:1px solid #cfdcc2}
.social-links{left:595px;top:1006px;font-size:11px;color:var(--green-dark)}
.social-icons{left:595px;top:1030px;display:flex;gap:5px}
.social-icons span{width:24px;height:22px;border-radius:3px;background:#3f6ea6}
.foot-rule{left:20px;top:1149px;width:792px;height:1px;background:#c6d6b6}
.legal{top:1165px;font-size:9px;color:var(--ink)}
</style>
</head>
<body>

<header class="site-header abs">
  <div class="brand abs">
    <span class="brand-mark"></span>
    <span class="brand-name">Delia's Dog<br>Grooming</span>
  </div>
  <nav class="main-nav abs">
    <a class="active" href="#">HOME</a>
    <a href="#" style="width:90px">ABOUT US</a>
    <a href="#" style="width:78px">GALLERY</a>
    <a href="#" style="width:114px">APPOINTMENT</a>
    <a href="#" style="width:94px">LOCATION</a>
    <a href="#" style="width:108px;font-size:13px">CONTACT</a>
  </nav>
</header>

<section class="hero abs">
  <div class="hero-panel abs">
    <h1 class="hero-title abs">Delia's Dog Grooming</h1>
    <div class="hero-punch abs">PUNCH LINE HERE..</div>
    <div class="hero-copy abs">
      <p>Brightpaw Studio is a web service company, offering a wide range of services which range from designing and development, that is covering almost all the fields in the best possible way.</p>
      <p>To be the best we know what and how to present beautifully the working of the client's need and their advantages be highlighted. We act in accordance with the Industry certified processes to deliver the best to our clients all over the world.</p>
    </div>
    <a class="btn hero-btn abs" href="#">View more breeds here</a>
    <div class="hero-photo abs" role="img" aria-label="Photo of a groomed schnauzer lying on a lawn"></div>
    <div class="slider-nav abs">
      <svg width="20" height="10" viewBox="0 0 20 10"><path d="M18 3 Q10 10 3 5 M3 5 L7 2 M3 5 L7 8" stroke="#7b1468" stroke-width="1.6" fill="none"/></svg>
      <span></span><span></span><span></span><span></span><span></span>
      <svg width="20" height="10" viewBox="0 0 20 10"><path d="M2 3 Q10 10 17 5 M17 5 L13 2 M17 5 L13 8" stroke="#7b1468" stroke-width="1.6" fill="none"/></svg>
    </div>
  </div>
</section>
<div class="hero-shadow abs"></div>

<main>
  <h2 class="section-title about-title dotted abs">A Little More About us</h2>
  <div class="about-copy abs">
    <p>Brightpaw Studio is a web service company, offering a wide range of services which range from designing and development, that is covering almost all the fields in the best possible way.<br>To be the best we know what and how to present beautifully the working of the client's need and their advantages be highlighted. We act in accordance with the Industry certified processes to deliver the best to our clients all over the world. Over years we have built a strong reputation in providing website design and web development services</p>
    <p>Brightpaw Studio is a professional website design company dedicated to provide excellent services. We at Brightpaw Studio think graphic design as a combination and collaboration of ideas and technology. Our Website Design team give an unforgettable impression on the customers and the clients. We can assure you that this is the best place for requirement of yours regarding website design solutions</p>
  </div>

  <h2 class="section-title gallery-title dotted abs">View Before After Dogs</h2>
  <div class="gallery abs">
    <div class="thumb" role="img" aria-label="Before and after grooming photo 1"></div>
    <div class="thumb" role="img" aria-label="Before and after grooming photo 2"></div>
    <div class="thumb" role="img" aria-label="Before and after grooming photo 3"></div>
    <div class="thumb" role="img" aria-label="Before and after grooming photo 4"></div>
    <div class="thumb alt" role="img" aria-label="Before and after grooming photo 5"></div>
    <div class="thumb alt" role="img" aria-label="Before and after grooming photo 6"></div>
    <div class="thumb" role="img" aria-label="Before and after grooming photo 7"></div>
    <div class="thumb" role="img" aria-label="Before and after grooming photo 8"></div>
  </div>
  <a class="view-all abs">VIEW ALL</a>

  <div class="divider abs"></div>

  <aside>
    <div class="appointment abs">
      <h2>Make an Appointment</h2>
      <p>The only way to success is through the right path and that's what we provide you. None of the other companies has the result we do. So stick to the best that's how you will be the best don't opt for the second best.</p>
      <a class="btn" href="#">Make appointment</a>
    </div>
    <h2 class="section-title rec-title abs">Recommended</h2>
    <div class="rec-item abs" style="top:669px">
      <div class="rec-thumb" role="img" aria-label="Recommended breed photo"></div>
      <div><h3>BREED NAME</h3><p>Brightpaw Studio is a web service company, offering a wide range of services which range from</p></div>
    </div>
    <div class="rec-item abs" style="top:750px">
      <div class="rec-thumb" role="img" aria-label="Recommended breed photo"></div>
      <div><h3>BREED NAME</h3><p>Brightpaw Studio is a web service company, offering a wide range of services which range from</p></div>
    </div>
    <div class="rec-item abs" style="top:830px">
      <div class="rec-thumb" role="img" aria-label="Recommended breed photo"></div>
      <div><h3>BREED NAME</h3><p>Brightpaw Studio is a web service company, offering a wide range of services which range from</p></div>
    </div>
  </aside>
</main>

<footer class="site-footer abs">
  <h4 class="foot-head abs" style="left:24px;top:24px">Archive Links</h4>
  <ul class="foot-links abs" style="left:24px;top:52px">
    <li>Home</li><li>About Us</li><li>Services</li><li>Gallery</li><li style="border:0">Latest Breed</li>
  </ul>
  <ul class="foot-links abs" style="left:188px;top:50px">
    <li>Latest Blog</li><li>News &amp; Artciles</li><li>Make an Appointment</li><li>Location</li><li style="border:0">Contact Us</li>
  </ul>
  <h4 class="foot-head abs" style="left:371px;top:24px">Category Here</h4>
  <ul class="foot-links abs" style="left:371px;top:46px">
    <li>Your Breed Goes here</li><li>Brreed Service here</li><li>Any other link</li><li>Best Breed</li>
  </ul>
  <h4 class="foot-head abs" style="left:592px;top:21px">Connect with us</h4>
</footer>
<div class="social-links abs">Pawbook &nbsp;|&nbsp; Chirper &nbsp;|&nbsp; Linkedly</div>
<div class="social-icons abs"><span></span><span></span><span></span></div>
<div class="foot-rule abs"></div>
<div class="legal abs" style="left:26px">Privacy Policy &nbsp;|&nbsp; Terms &amp; Conditions</div>
<div class="legal abs" style="right:50px">Copyright © 2012 Company Name &nbsp;|&nbsp; All right reserved</div>

</body>
</html>
```